Marlith Construction Core Values Wall Design

Core Values Wall Design for our Wall, I’m not exactly sure visually what we would want it to look like. Maybe some acrylic stand offs that could go on brick? If that’s a possibility. That’s where we have the most space in the office. But we could do other locations too.

These are our core values
• Safety
• Integrity
• Quality
• Client-Focused Solutions
• Continuous Improvement
• Positive Culture and Stewardship

Our vision/mission statement is Craft Assured.

```html
<!DOCTYPE html>
<html lang="en">
<head>
<meta charset="utf-8">
<title>Marlith Construction – Core Values</title>
<link href="https://fonts.googleapis.com/css2?family=Oswald:wght@500;600;700&display=swap" rel="stylesheet">
<style>
  :root {
    --plate: #dcd8da;
    --plate-light: #ece9ea;
    --red: #e8232b;
    --mint: #8fe0bf;
    --purple: #8a5cf0;
    --yellow: #efbd36;
    --sky: #5fb0f2;
    --navy: #0b5a9c;
    --white: #ffffff;
    --ink-shadow: rgba(60, 50, 55, 0.25);
  }
  * { margin: 0; padding: 0; box-sizing: border-box; }
  html, body { width: 1200px; height: 800px; overflow: hidden; }
  body {
    background: radial-gradient(circle at 70% 45%, var(--plate-light), var(--plate) 70%);
    font-family: "Oswald", "Arial Narrow", sans-serif;
    position: relative;
  }
  .values-wheel { position: absolute; inset: 0; }
  .value-label {
    position: absolute;
    font-weight: 600;
    text-transform: uppercase;
    line-height: 1.02;
    letter-spacing: 0.5px;
  }
  .value-label--client { left: 200px; top: 98px; font-size: 27px; color: var(--red); text-align: center; }
  .value-label--quality { left: 140px; top: 262px; font-size: 28px; color: var(--yellow); }
  .value-label--integrity { left: 86px; top: 410px; font-size: 28px; color: var(--sky); }
  .value-label--safety { left: 240px; top: 680px; font-size: 28px; color: var(--navy); }
  .value-label--improvement { left: 618px; top: 118px; font-size: 24px; color: var(--mint); }
  .value-label--culture { left: 760px; top: 228px; font-size: 24px; color: var(--purple); text-align: center; }
  .headline {
    position: absolute;
    left: 640px;
    top: 470px;
    font-weight: 700;
    font-size: 92px;
    line-height: 0.95;
    color: var(--white);
    text-shadow: 0 2px 6px var(--ink-shadow);
    text-transform: uppercase;
  }
  .brand-name {
    position: absolute;
    right: 90px;
    top: 150px;
    font-weight: 600;
    font-size: 38px;
    line-height: 1.05;
    color: var(--red);
    text-transform: uppercase;
    text-align: right;
  }
  .brand-name span { display: block; font-size: 21px; letter-spacing: 7px; }
  .tagline {
    position: absolute;
    right: 90px;
    top: 680px;
    font-weight: 600;
    font-size: 30px;
    color: var(--navy);
    text-transform: uppercase;
    letter-spacing: 1px;
  }
</style>
</head>
<body>
  <svg class="values-wheel" width="1200" height="800" viewBox="0 0 1200 800" aria-hidden="true">
    <g class="segments" stroke="var(--plate)" stroke-width="7" stroke-linejoin="round">
      <path fill="var(--red)" d="M323.2 223.2 A250 250 0 0 1 500 150 L500 250 A150 150 0 0 0 393.9 293.9 Z"/>
      <path fill="var(--mint)" d="M500 150 A250 250 0 0 1 676.8 223.2 L606.1 293.9 A150 150 0 0 0 500 250 Z"/>
      <path fill="var(--purple)" d="M676.8 223.2 A250 250 0 0 1 750 400 L650 400 A150 150 0 0 0 606.1 293.9 Z"/>
      <path fill="var(--navy)" d="M500 650 A250 250 0 0 1 323.2 576.8 L393.9 506.1 A150 150 0 0 0 500 550 Z"/>
      <path fill="var(--sky)" d="M323.2 576.8 A250 250 0 0 1 250 400 L350 400 A150 150 0 0 0 393.9 506.1 Z"/>
      <path fill="var(--yellow)" d="M250 400 A250 250 0 0 1 323.2 223.2 L393.9 293.9 A150 150 0 0 0 350 400 Z"/>
    </g>

    <g class="hub" fill="none" stroke="var(--white)">
      <circle cx="500" cy="400" r="92" stroke-width="9"/>
      <circle cx="500" cy="400" r="30" stroke-width="14" stroke-dasharray="9 6.7"/>
      <circle cx="500" cy="400" r="24" stroke-width="9"/>
    </g>

    <g class="icons" fill="none" stroke="var(--white)" stroke-width="3" stroke-linecap="round" stroke-linejoin="round">
      <!-- lightbulb -->
      <g transform="translate(423.5 215.2)">
        <path d="M-10 8 C-20 0 -16 -20 0 -20 C16 -20 20 0 10 8 L8 16 L-8 16 Z"/>
        <path d="M-6 22 H6"/><path d="M-6 -4 L-2 1 L6 -8"/>
      </g>
      <!-- bar chart -->
      <g transform="translate(576.5 215.2)">
        <rect x="-20" y="2" width="8" height="16"/><rect x="-6" y="-8" width="8" height="26"/><rect x="8" y="6" width="8" height="12"/>
        <path d="M-2 -14 V-24 M-6 -20 L-2 -24 L2 -20"/>
      </g>
      <!-- stars -->
      <g transform="translate(684.8 323.5)">
        <path d="M-10 -12 l3 6 6 1 -5 4 1 6 -5 -3 -5 3 1 -6 -5 -4 6 -1 Z"/>
        <path d="M12 -2 l3 6 6 1 -5 4 1 6 -5 -3 -5 3 1 -6 -5 -4 6 -1 Z"/>
        <path d="M-20 18 H22"/>
      </g>
      <!-- shield tick -->
      <g transform="translate(423.5 584.8)">
        <path d="M0 -22 L18 -15 V0 C18 12 8 19 0 23 C-8 19 -18 12 -18 0 V-15 Z"/>
        <path d="M-8 0 L-2 6 L9 -6"/>
      </g>
      <!-- small shield tick -->
      <g transform="translate(315.2 476.5)">
        <path d="M0 -16 L13 -11 V0 C13 9 6 14 0 17 C-6 14 -13 9 -13 0 V-11 Z"/>
        <path d="M-6 0 L-1 5 L7 -4"/>
      </g>
      <!-- diamond -->
      <g transform="translate(315.2 323.5)">
        <path d="M-18 -8 L-10 -18 H10 L18 -8 L0 16 Z"/>
        <path d="M-18 -8 H18 M-6 -8 L0 16 L6 -8"/>
      </g>
    </g>

    <g class="leaders" fill="none" stroke="#555" stroke-width="2" stroke-dasharray="2 5">
      <path d="M390 106 H470 V190"/>
      <path d="M268 280 H340"/>
      <path d="M226 430 H290 V410"/>
      <path d="M360 698 H410 V670"/>
      <path d="M610 140 H585 V180"/>
      <path d="M865 318 V345 H820"/>
    </g>
  </svg>

  <div class="value-label value-label--client">Client-Focused<br>Solutions</div>
  <div class="value-label value-label--quality">Quality</div>
  <div class="value-label value-label--integrity">Integrity</div>
  <div class="value-label value-label--safety">Safety</div>
  <div class="value-label value-label--improvement">Continuous<br>Improvement</div>
  <div class="value-label value-label--culture">Positive<br>Culture and<br>Stewardship</div>

  <h1 class="headline">Core<br>Values</h1>

  <div class="brand-name">Marlith<span>Construction</span></div>
  <div class="tagline">Craft Assured</div>
</body>
</html>
```